Dental Practice Billboard Design

We are a newer dental practice in need of a simple but appealing billboard for our growing dental practice to attract new patients. The practice is owned by husband and wife dentists and is family friendly in a small town in Kentucky. We try to be very friendly and caring to our patients. Would prefer a blue background for the billboard and our tooth logo to be prominent. We are partial to the Patua One font used in the image below but please feel free to tweak it as you deem necessary. The shape of the uppercase D and lowercase g are why we like that font, so fonts with a similarly shaped “D” and “g” would work as well. Please include our phone number (555) 847-1390. Please see our website Harlowbrookdentistry.example for more info on the practice if needed. Thank you! Looking forward to seeing your creation.
Updates

The dimensions will be 12ft x 24ft (3.6576m x 7.3152m). Apologies for not including this in the original prompt. Thank you all for your submissions.

Industry/Entity Type

Dental

Font styles to use
Other font styles liked:
• Patua One

Colors
0054AA
0677BA
7BADD7
CADEEF
E8F1F8
0094D4
00A9DD
6FCCEA
C7EBF8
E9F6FB
00AB8E
00BBA5
67D7C9
C6EFE9
E9F9F6
59FF00
82FF00
B8FF75
E3FFCB
F4FFEA

Requirements
Must have
• Phone number, website, Logo, Practice name “Harlow Brook Dentistry”
Should not have
• A tagline or slogan

```html
<!DOCTYPE html>
<html lang="en">
<head>
<meta charset="utf-8">
<title>Harlow Brook Dentistry Billboard</title>
<link href="https://fonts.googleapis.com/css2?family=Patua+One&display=swap" rel="stylesheet">
<style>
  :root {
    --board-blue: #2a4faa;
    --accent-green: #35a83a;
    --ink-white: #f4f4ef;
    --page-bg: #e8f1f8;
  }
  * { margin: 0; padding: 0; box-sizing: border-box; }
  html, body {
    width: 1200px;
    height: 900px;
    overflow: hidden;
    background: var(--page-bg);
  }
  .billboard {
    position: absolute;
    left: 40px;
    top: 170px;
    width: 1120px;
    height: 560px;
    background: var(--board-blue);
    font-family: "Patua One", Georgia, serif;
    color: var(--ink-white);
  }
  .brand-mark {
    position: absolute;
    left: 60px;
    top: 160px;
    width: 230px;
    display: flex;
    flex-direction: column;
    align-items: center;
    gap: 24px;
  }
  .brand-mark__dot {
    width: 130px;
    height: 130px;
    border-radius: 50%;
    background: var(--ink-white);
  }
  .brand-mark__name {
    font-size: 34px;
    line-height: 1.1;
    text-align: center;
  }
  .practice-name {
    position: absolute;
    left: 335px;
    top: 120px;
    width: 735px;
    text-align: center;
    font-size: 68px;
    line-height: 1;
    font-weight: 400;
    white-space: nowrap;
  }
  .website-pill {
    position: absolute;
    left: 335px;
    top: 222px;
    width: 735px;
    height: 86px;
    border-radius: 43px;
    background: var(--accent-green);
    display: flex;
    align-items: center;
    justify-content: center;
    font-size: 42px;
    letter-spacing: 1px;
    white-space: nowrap;
  }
  .phone {
    position: absolute;
    left: 335px;
    top: 340px;
    width: 735px;
    text-align: center;
    font-size: 96px;
    line-height: 1;
    white-space: nowrap;
  }
</style>
</head>
<body>
  <section class="billboard">
    <div class="brand-mark">
      <div class="brand-mark__dot"></div>
      <div class="brand-mark__name">Harlow Brook Dentistry</div>
    </div>
    <h1 class="practice-name">Harlow Brook Dentistry</h1>
    <p class="website-pill">Harlowbrookdentistry.example</p>
    <p class="phone">(555) 847-1390</p>
  </section>
</body>
</html>
```